Oil and Gas Exploration and Production company needs a business card design

We need a business card design using our logo and colors in the logo. We want a mainstream design.

```html
<!DOCTYPE html>
<html lang="en">
<head>
<meta charset="utf-8">
<title>Corvia Oil &amp; Gas — Business Card</title>
<link href="https://fonts.googleapis.com/css2?family=Arimo:wght@400;700&display=swap" rel="stylesheet">
<style>
  :root {
    --ink: #0b0b0b;
    --gold: #c99a34;
    --paper: #ffffff;
    --backdrop: #e8e6e2;
    --text: #111111;
  }
  * { margin: 0; padding: 0; box-sizing: border-box; }
  html, body {
    width: 1200px;
    height: 902px;
    overflow: hidden;
    background: var(--backdrop);
    font-family: "Arimo", Arial, sans-serif;
  }
  .card {
    position: absolute;
    left: 80px;
    top: 154px;
    width: 1040px;
    height: 594px;
    background: var(--paper);
    overflow: hidden;
    box-shadow: 0 10px 30px rgba(0,0,0,0.18);
  }
  .card__shapes {
    position: absolute;
    inset: 0;
    width: 1040px;
    height: 594px;
  }
  .brand {
    position: absolute;
    left: 60px;
    top: 82px;
    display: flex;
    align-items: center;
    gap: 20px;
  }
  .brand__dot {
    width: 74px;
    height: 74px;
    border-radius: 50%;
    background: var(--ink);
    flex: none;
  }
  .brand__name {
    color: var(--ink);
    font-weight: 700;
    line-height: 1;
  }
  .brand__name-main {
    display: block;
    font-size: 104px;
    letter-spacing: -2px;
  }
  .brand__name-sub {
    display: block;
    font-size: 38px;
    letter-spacing: 7px;
    margin-top: 6px;
    text-transform: uppercase;
  }
  .tab {
    position: absolute;
    left: -28px;
    top: 302px;
    width: 56px;
    height: 56px;
    border-radius: 50%;
    background: var(--gold);
  }
  .person {
    position: absolute;
    left: 59px;
    top: 300px;
  }
  .person__name {
    font-size: 34px;
    font-weight: 700;
    color: var(--text);
    line-height: 36px;
  }
  .person__role {
    font-size: 25px;
    color: var(--gold);
    line-height: 28px;
  }
  .address {
    position: absolute;
    left: 59px;
    top: 380px;
    font-size: 25px;
    line-height: 33px;
    color: var(--text);
    font-style: normal;
  }
  .contacts {
    position: absolute;
    left: 61px;
    top: 461px;
    list-style: none;
    font-size: 24px;
    color: var(--text);
  }
  .contacts__item {
    display: flex;
    align-items: center;
    gap: 14px;
    height: 31px;
  }
  .contacts__icon {
    width: 24px;
    height: 24px;
    flex: none;
  }
</style>
</head>
<body>
  <article class="card">
    <svg class="card__shapes" viewBox="0 0 1040 594" aria-hidden="true">
      <rect width="1040" height="594" fill="var(--ink)"/>
      <path d="M0 0 H841 C935 80 965 330 827 594 H0 Z" fill="var(--paper)"/>
      <path d="M926 275 C918 420 868 525 812 594 H636 C770 545 890 440 926 275 Z" fill="var(--gold)"/>
    </svg>

    <div class="brand">
      <span class="brand__dot"></span>
      <div class="brand__name">
        <span class="brand__name-main">Corvia</span>
        <span class="brand__name-sub">Oil &amp; Gas</span>
      </div>
    </div>

    <span class="tab"></span>

    <div class="person">
      <p class="person__name">Daniel Reyes</p>
      <p class="person__role">President &amp; CEO</p>
    </div>

    <address class="address">
      PO BOX 456, Harbor Road<br>
      4th Lane, Leeds
    </address>

    <ul class="contacts">
      <li class="contacts__item">
        <svg class="contacts__icon" viewBox="0 0 24 24" aria-hidden="true">
          <path d="M3 8 C3 5 7 4 12 4 C17 4 21 5 21 8 V10 H16 V8 H8 V10 H3 Z" fill="var(--gold)"/>
          <path d="M6 11 H18 L20 19 H4 Z" fill="var(--gold)"/>
          <circle cx="12" cy="15" r="2.2" fill="var(--paper)"/>
        </svg>
        (123) 555 0142
      </li>
      <li class="contacts__item">
        <svg class="contacts__icon" viewBox="0 0 24 24" aria-hidden="true">
          <rect x="2" y="5" width="20" height="14" fill="var(--gold)"/>
          <path d="M2 5 L12 13 L22 5 M2 19 L9 11 M22 19 L15 11" stroke="var(--paper)" stroke-width="1.5" fill="none"/>
        </svg>
        hello@corviaenergy.com
      </li>
      <li class="contacts__item">
        <svg class="contacts__icon" viewBox="0 0 24 24" aria-hidden="true">
          <circle cx="12" cy="12" r="10" fill="var(--gold)"/>
          <g stroke="var(--paper)" stroke-width="1.3" fill="none">
            <ellipse cx="12" cy="12" rx="4.5" ry="10"/>
            <line x1="2" y1="12" x2="22" y2="12"/>
            <line x1="12" y1="2" x2="12" y2="22"/>
            <path d="M4 7 H20 M4 17 H20"/>
          </g>
        </svg>
        www.corviaenergy.com
      </li>
    </ul>
  </article>
</body>
</html>
```